Tiskoro

We need a business card for our company is a holding for different business all are different we try to have some air of relax and fun in our projects we add pictures of the office to give you an idea od the mood of the business

Business

```html
<!DOCTYPE html>
<html lang="en">
<head>
<meta charset="utf-8">
<title>Tiskoro business card</title>
<link rel="stylesheet" href="https://fonts.googleapis.com/css2?family=Michroma&family=Exo+2:wght@400;700&display=swap">
<style>
  :root {
    --bg: #e6e4e1;
    --card: #f7f7f6;
    --brown: #6b4427;
    --yellow: #f7e330;
    --yellow-shade: #e8cf1d;
    --ink: #2b2b2b;
    --ink-soft: #555;
  }
  * { margin: 0; padding: 0; box-sizing: border-box; }
  html, body { width: 1200px; height: 1059px; overflow: hidden; background: var(--bg); }
  .canvas { position: relative; width: 1200px; height: 1059px; }
  .card {
    position: absolute; left: 180px; width: 840px; height: 480px;
    background: var(--card); box-shadow: 0 6px 18px rgba(0,0,0,.15); overflow: hidden;
  }
  .card--front { top: 40px; }
  .card--back { top: 545px; }
  .stripes { position: absolute; inset: 0; }
  .brand {
    position: absolute; display: flex; align-items: center; gap: 10px;
    font-family: "Exo 2", sans-serif; font-weight: 700; color: var(--brown); line-height: 1;
  }
  .brand__mark { background: var(--yellow); }
  .card--front .brand { left: 40px; top: 160px; font-size: 34px; }
  .card--front .brand__mark { width: 26px; height: 26px; }
  .card--back .brand { left: 50%; top: 50%; transform: translate(-50%, -50%); font-size: 64px; gap: 16px; }
  .card--back .brand__mark { width: 48px; height: 48px; }
  .person { position: absolute; right: 40px; top: 30px; text-align: right; }
  .person__name { font-family: "Michroma", sans-serif; font-size: 30px; color: var(--ink); letter-spacing: 1px; }
  .person__role { font-family: "Michroma", sans-serif; font-size: 15px; color: var(--ink-soft); letter-spacing: 2px; margin-top: 6px; }
  .address {
    position: absolute; right: 40px; top: 200px;
    font-family: "Exo 2", sans-serif; font-size: 17px; color: var(--ink);
  }
  .contacts {
    position: absolute; right: 40px; top: 332px; list-style: none;
    font-family: "Exo 2", sans-serif; font-size: 17px; color: var(--ink);
  }
  .contacts li { display: flex; justify-content: flex-end; align-items: center; gap: 10px; height: 27px; }
  .contacts svg { width: 16px; height: 16px; fill: var(--ink); }
</style>
</head>
<body>
<div class="canvas">
  <section class="card card--front">
    <svg class="stripes" viewBox="0 0 840 480" aria-hidden="true">
      <rect x="0" y="80" width="300" height="40" fill="var(--brown)"/>
      <polygon points="300,80 360,140 360,180 300,120" fill="var(--yellow)"/>
      <rect x="360" y="140" width="480" height="40" fill="var(--brown)"/>
      <rect x="0" y="240" width="380" height="40" fill="var(--brown)"/>
      <polygon points="380,240 440,290 440,330 380,280" fill="var(--yellow-shade)"/>
      <rect x="440" y="290" width="400" height="40" fill="var(--brown)"/>
    </svg>
    <div class="brand"><span class="brand__mark"></span>Tiskoro</div>
    <div class="person">
      <div class="person__name">DANIEL REYES</div>
      <div class="person__role">FINANCIAL ADVISOR</div>
    </div>
    <div class="address">042 12th Floor Harbor View Road RKT</div>
    <ul class="contacts">
      <li>014 552 7810
        <svg viewBox="0 0 16 16"><path d="M3 1l3 3-2 2c1 2 3 4 5 5l2-2 3 3-2 3C6 14 2 10 1 3z"/></svg></li>
      <li>014 552 7810
        <svg viewBox="0 0 16 16"><path d="M4 0h8v16H4zM5 2v10h6V2z"/></svg></li>
      <li>014 552 7810
        <svg viewBox="0 0 16 16"><path d="M1 5h14v10H1zM4 0h8v4H4zM3 8h2v2H3zm4 0h2v2H7zm4 0h2v2h-2z"/></svg></li>
      <li>hello@tiskoro.com
        <svg viewBox="0 0 16 16"><path d="M0 3h16v10H0zM1 4l7 5 7-5v-.5H1z"/></svg></li>
      <li>www.tiskoro.com
        <svg viewBox="0 0 16 16"><circle cx="8" cy="8" r="7" fill="none" stroke="#2b2b2b" stroke-width="1.5"/><path d="M1 8h14M8 1v14" stroke="#2b2b2b" stroke-width="1.2"/></svg></li>
    </ul>
  </section>

  <section class="card card--back">
    <div class="brand"><span class="brand__mark"></span>Tiskoro</div>
  </section>
</div>
</body>
</html>
```